CLAIM GUARD PLAN

I'm virtually ready to launch my site, but I have a number of edits and modifications that need to be implemented. More importantly, I'm always looking to improve my site, particularly now that I am making my proverbial "FIRST IMPRESSION." Thus, I'm willing to see if there is someone who can add creativity and perhaps improve what I already have, particularly on the All Important Front Page.

```html
<!DOCTYPE html>
<html lang="en">
<head>
<meta charset="utf-8">
<title>Claim Guard Plan</title>
<link href="https://fonts.googleapis.com/css2?family=Montserrat:wght@400;500;600;700&family=Lato:wght@400;700&display=swap" rel="stylesheet">
<style>
:root{
  --navy:#0a1f4d;
  --navy-deep:#02204f;
  --red:#a50010;
  --red-bright:#c4141f;
  --ink:#1c1c1c;
  --grey:#cfcfcf;
  --white:#ffffff;
  --black:#000000;
}
*{box-sizing:border-box;margin:0;padding:0}
html,body{width:1200px;height:3345px;overflow:hidden}
body{position:relative;background:var(--white);font-family:'Lato',sans-serif;color:var(--ink)}
.abs{position:absolute}
.heading{font-family:'Montserrat',sans-serif}

/* header */
.site-header{position:absolute;left:0;top:0;width:1200px;height:86px;background:var(--white);z-index:3}
.brand-badge{position:absolute;left:103px;top:2px;width:124px;height:124px;border-radius:50%;background:var(--white);display:flex;align-items:center;justify-content:center;z-index:4}
.brand-badge .disc{width:106px;height:106px;border-radius:50%;background:var(--navy);display:flex;align-items:center;justify-content:center;text-align:center;color:var(--white);font-family:'Montserrat',sans-serif;font-weight:700;font-size:13px;line-height:1.2}
.nav{position:absolute;top:33px;font-family:'Montserrat',sans-serif;font-size:16px;color:#222;letter-spacing:.3px}
.call-btn{position:absolute;left:926px;top:17px;width:172px;height:51px;background:var(--navy);color:var(--white);border-radius:3px;display:flex;align-items:center;justify-content:center;gap:12px;font-family:'Montserrat',sans-serif;font-weight:700;font-size:16px}

/* hero */
.hero{position:absolute;left:0;top:86px;width:1200px;height:599px;background:linear-gradient(100deg,#121a24 0%,#2b3744 45%,#4a5560 70%,#2a323c 100%)}
.hero-shade{position:absolute;inset:0;background:linear-gradient(90deg,rgba(0,0,0,.55),rgba(0,0,0,.1) 70%)}
.hero-title{position:absolute;left:96px;top:160px;font-family:'Montserrat',sans-serif;font-weight:700;font-size:50px;color:var(--white);letter-spacing:.5px}
.hero-text{position:absolute;left:101px;top:230px;width:500px;color:var(--white);font-size:15.5px;line-height:31px}
.btn-red{position:absolute;left:101px;top:377px;width:303px;height:50px;background:var(--red);color:var(--white);font-family:'Montserrat',sans-serif;font-weight:700;font-size:16px;display:flex;align-items:center;justify-content:center;border-radius:3px}

/* services */
.section-title{position:absolute;left:0;width:1200px;text-align:center;font-family:'Montserrat',sans-serif;font-weight:600;font-size:32px;color:var(--navy)}
.services-intro{position:absolute;left:160px;top:822px;width:880px;text-align:center;font-size:17px;line-height:35px;color:#333}
.services-intro b{color:var(--navy)}
.service-card{position:absolute;width:321px;height:239px;border:3px solid var(--navy);border-radius:8px;background:var(--white);box-shadow:0 4px 12px rgba(0,0,0,.12);display:flex;flex-direction:column;align-items:center;justify-content:center;text-align:center}
.service-card.red{border-color:var(--red-bright)}
.service-card svg{width:72px;height:72px;margin-bottom:18px}
.service-name{font-family:'Montserrat',sans-serif;font-weight:500;font-size:16px;line-height:31px;color:#111;letter-spacing:.3px;max-width:240px}
.learn-more{margin-top:14px;font-family:'Montserrat',sans-serif;font-size:15px;color:#111;text-decoration:underline;letter-spacing:.3px}

/* about + form */
.about{position:absolute;left:0;top:1539px;width:703px;height:582px;background:var(--navy-deep);color:var(--white)}
.about h2{position:absolute;left:99px;top:78px;font-family:'Montserrat',sans-serif;font-weight:600;font-size:32px;word-spacing:8px}
.about p{position:absolute;left:99px;width:520px;font-size:15px;line-height:31px}
.btn-grey{position:absolute;left:99px;top:443px;width:132px;height:46px;background:var(--grey);color:var(--navy);font-family:'Montserrat',sans-serif;font-weight:700;font-size:16px;display:flex;align-items:center;justify-content:center;border-radius:2px}
.consult{position:absolute;left:711px;top:1539px;width:489px;height:582px;background:var(--red)}
.consult h2{position:absolute;left:0;top:64px;width:489px;text-align:center;padding-left:8px;font-family:'Montserrat',sans-serif;font-weight:600;font-size:32px;color:var(--white)}
.field{position:absolute;left:47px;width:381px;background:var(--white);font-size:15px;color:#333;padding:0 23px;display:flex;align-items:center}
.field.tall{align-items:flex-start;padding-top:18px}
.btn-navy{position:absolute;left:177px;top:462px;width:133px;height:47px;background:var(--navy);color:var(--white);font-family:'Montserrat',sans-serif;font-weight:700;font-size:16px;display:flex;align-items:center;justify-content:center;border-radius:3px}

/* faq */
.faq-item{position:absolute;left:144px;width:911px;border:1.5px solid #333;border-radius:2px;padding:0 22px;font-family:'Montserrat',sans-serif;color:#111}
.faq-q{font-size:18px;line-height:31px}
.faq-q.small{font-size:16px}
.faq-toggle{position:absolute;right:22px;width:16px;height:16px}
.faq-answer{margin-top:12px;border-left:3px solid var(--red-bright);padding-left:16px;font-family:'Lato',sans-serif;font-size:14.5px;line-height:31px;color:#333}

/* footer */
.footer{position:absolute;left:0;top:2919px;width:1200px;height:426px;background:var(--black);color:var(--white)}
.footer-badge{position:absolute;left:100px;top:74px;width:169px;height:169px;border-radius:50%;background:var(--navy);display:flex;align-items:center;justify-content:center;text-align:center;font-family:'Montserrat',sans-serif;font-weight:700;font-size:18px;line-height:1.25}
.footer h3{position:absolute;top:79px;font-family:'Montserrat',sans-serif;font-weight:600;font-size:21px}
.footer-links{position:absolute;top:121px;list-style:none;font-size:15px;line-height:31px;font-family:'Lato',sans-serif;letter-spacing:.3px}
.footer-links li{display:flex;align-items:center;gap:12px}
.contact-row{position:absolute;left:800px;display:flex;gap:12px;font-size:15px;line-height:31px}
.contact-icon{flex:none;width:36px;height:36px;border-radius:50%;background:var(--red);display:flex;align-items:center;justify-content:center}
.footer-rule{position:absolute;left:100px;top:364px;width:1001px;height:1px;background:#777}
.copyright{position:absolute;left:100px;top:380px;font-size:15px}
.social{position:absolute;top:380px;width:24px;height:24px;border-radius:50%;background:var(--red-bright)}
</style>
</head>
<body>

<header class="site-header">
  <span class="nav" style="left:378px">HOME</span>
  <span class="nav" style="left:477px">ABOUT</span>
  <span class="nav" style="left:582px">SERVICES</span>
  <span class="nav" style="left:708px">FAQ</span>
  <span class="nav" style="left:790px">CONTACT US</span>
  <div class="call-btn">
    <svg width="16" height="16" viewBox="0 0 24 24"><path fill="#fff" d="M6.6 10.8a15.1 15.1 0 0 0 6.6 6.6l2.2-2.2c.3-.3.7-.4 1-.2 1.1.4 2.3.6 3.6.6.6 0 1 .4 1 1V20c0 .6-.4 1-1 1A17 17 0 0 1 3 4c0-.6.4-1 1-1h3.5c.6 0 1 .4 1 1 0 1.3.2 2.5.6 3.6.1.3 0 .7-.2 1z"/></svg>
    555.010.4477
  </div>
</header>
<div class="brand-badge"><div class="disc">CLAIM<br>GUARD<br>PLAN</div></div>

<section class="hero" role="img" aria-label="Photo of a businesswoman walking through a modern glass office with colleagues at a meeting table">
  <div class="hero-shade"></div>
  <h1 class="hero-title">CLAIM GUARD PLAN</h1>
  <p class="hero-text">BUSINESS OWNERS: Claim Guard Plan (CGP) Is An Extremely Affordable Legal Service Plan (As Little As $8.00 Per Month) That INSULATES Business Owners From Unwarranted LEGAL CLAIMS And Expensive LAWSUITS.</p>
  <div class="btn-red">SCHEDULE FREE CONSULATION</div>
</section>

<h2 class="section-title" style="top:764px">OUR SERVICES</h2>
<p class="services-intro">The price for a membership is a ridiculously low <b>$9.95 PER WEEK.</b> We believe that this fee is very affordable. So what is it? Membership includes the following:</p>

<div class="service-card" style="left:99px;top:933px">
  <svg viewBox="0 0 64 64" fill="none" stroke-width="2"><circle cx="32" cy="20" r="7" stroke="#a50010"/><path d="M20 40c0-8 5-12 12-12s12 4 12 12" stroke="#0a1f4d"/><path d="M10 42h44M16 42v14M48 42v14" stroke="#a50010"/><rect x="26" y="4" width="14" height="8" rx="1" stroke="#0a1f4d"/></svg>
  <div class="service-name">FREE INITIAL CONSULTATION</div>
  <div class="learn-more">LEARN MORE</div>
</div>
<div class="service-card red" style="left:442px;top:933px">
  <svg viewBox="0 0 64 64" fill="none" stroke-width="2"><circle cx="36" cy="26" r="20" stroke="#0a1f4d" stroke-dasharray="3 3"/><rect x="28" y="16" width="18" height="22" stroke="#0a1f4d"/><rect x="12" y="38" width="16" height="14" rx="2" stroke="#a50010"/><path d="M15 38v-5a5 5 0 0 1 10 0v5" stroke="#a50010"/></svg>
  <div class="service-name">PROPRIETARY CONTRACT LANGUAGE</div>
  <div class="learn-more">LEARN MORE</div>
</div>
<div class="service-card" style="left:783px;top:933px">
  <svg viewBox="0 0 64 64" fill="none" stroke-width="2"><circle cx="18" cy="22" r="5" stroke="#a50010"/><circle cx="46" cy="22" r="5" stroke="#a50010"/><path d="M8 44c0-8 4-12 10-12M56 44c0-8-4-12-10-12" stroke="#a50010"/><rect x="24" y="6" width="16" height="10" rx="2" stroke="#0a1f4d"/><path d="M20 40h24" stroke="#0a1f4d"/></svg>
  <div class="service-name">FREE CONSULTATION</div>
  <div class="learn-more">LEARN MORE</div>
</div>
<div class="service-card red" style="left:99px;top:1195px">
  <svg viewBox="0 0 64 64" fill="none" stroke-width="2"><rect x="10" y="6" width="32" height="44" rx="2" stroke="#0a1f4d"/><path d="M16 18h20M16 26h20M16 34h12" stroke="#0a1f4d"/><path d="M30 46l10-8 12 6-8 10z" stroke="#a50010"/></svg>
  <div class="service-name">FREE ATTORNEY LETTERS</div>
  <div class="learn-more">LEARN MORE</div>
</div>
<div class="service-card" style="left:442px;top:1195px">
  <svg viewBox="0 0 64 64" fill="none" stroke-width="2"><circle cx="36" cy="20" r="14" stroke="#0a1f4d"/><path d="M30 26l12-12" stroke="#0a1f4d"/><circle cx="31" cy="15" r="2" stroke="#0a1f4d"/><circle cx="41" cy="25" r="2" stroke="#0a1f4d"/><path d="M8 42h10l10 4h14l12-8" stroke="#a50010"/><rect x="6" y="40" width="6" height="16" stroke="#a50010"/></svg>
  <div class="service-name">LITIGATION DISCOUNTS</div>
  <div class="learn-more">LEARN MORE</div>
</div>
<div class="service-card red" style="left:783px;top:1195px">
  <svg viewBox="0 0 64 64" fill="none" stroke-width="2"><rect x="6" y="6" width="14" height="20" stroke="#0a1f4d"/><rect x="25" y="6" width="14" height="20" stroke="#0a1f4d"/><rect x="44" y="6" width="14" height="20" stroke="#0a1f4d"/><path d="M32 30v10M18 40l14 8 14-8M14 50h36" stroke="#a50010"/></svg>
  <div class="service-name">COLLECTIONS</div>
  <div class="learn-more">LEARN MORE</div>
</div>

<section class="about">
  <h2>ABOUT US</h2>
  <p style="top:137px">CGP is a group of attorney and legal assistants with many years of experience in litigation, who are devoted to <b>PREVENTING LEGAL</b> CLAIMS and COSTLY LAWSUITS through a variety of <b>FREE</b> and <b>VERY AFFORDABLE</b> services described below. <b>OUR UNIQUE SERVICE PLAN MAKES IT POSSIBLE FOR US TO PREVENT THE LAWSUITS.</b></p>
  <p style="top:323px">A homebuilding company was sued by a former employee who claimed to have been promised a more favorable sales area, which claim was disputed by the homebuilder.</p>
  <div class="btn-grey">Read More</div>
</section>

<section class="consult">
  <h2>Get A Free Consultation</h2>
  <div class="field" style="top:130px;height:53px">Full Name</div>
  <div class="field" style="top:199px;height:52px">Phone</div>
  <div class="field" style="top:266px;height:53px">Email</div>
  <div class="field tall" style="top:334px;height:108px">Message</div>
  <div class="btn-navy">Submit</div>
</section>

<h2 class="section-title" style="top:2197px">FREQUENTLY ASKED QUESTIONS</h2>

<div class="faq-item" style="top:2270px;height:149px;padding-top:18px">
  <div class="faq-q">Why should I be concerned about legal claims?</div>
  <svg class="faq-toggle" style="top:34px" viewBox="0 0 16 16"><circle cx="8" cy="8" r="8" fill="#a50010"/><rect x="4" y="7" width="8" height="2" fill="#fff"/></svg>
  <div class="faq-answer">Lorem ipsum dolor sit amet, consectetur adipiscing elit. Suspendisse varius enim in eros elementum tristique.<br>Duis cursus, mi quis viverra ornare, eros dolor interdum nulla, ut commodo diam libero vitae erat.</div>
</div>
<div class="faq-item" style="top:2449px;height:72px;display:flex;align-items:center">
  <div class="faq-q small">Provide more details about the value of CGP's contract language.</div>
  <svg class="faq-toggle" style="top:27px" viewBox="0 0 16 16"><circle cx="8" cy="8" r="8" fill="#0a1f4d"/><rect x="4" y="7" width="8" height="2" fill="#fff"/><rect x="7" y="4" width="2" height="8" fill="#fff"/></svg>
</div>
<div class="faq-item" style="top:2554px;height:72px;display:flex;align-items:center">
  <div class="faq-q small" style="font-size:15.5px;max-width:680px">If I'm a contractor, for example, how can an CGP membership minimize legal claims against my business?</div>
  <svg class="faq-toggle" style="top:27px" viewBox="0 0 16 16"><circle cx="8" cy="8" r="8" fill="#0a1f4d"/><rect x="4" y="7" width="8" height="2" fill="#fff"/><rect x="7" y="4" width="2" height="8" fill="#fff"/></svg>
</div>
<div class="faq-item" style="top:2656px;height:72px;display:flex;align-items:center">
  <div class="faq-q small">What does an CGP membership cost?</div>
  <svg class="faq-toggle" style="top:27px" viewBox="0 0 16 16"><circle cx="8" cy="8" r="8" fill="#0a1f4d"/><rect x="4" y="7" width="8" height="2" fill="#fff"/><rect x="7" y="4" width="2" height="8" fill="#fff"/></svg>
</div>
<div class="faq-item" style="top:2758px;height:72px;display:flex;align-items:center">
  <div class="faq-q small">Do you have a Referral Program?</div>
  <svg class="faq-toggle" style="top:27px" viewBox="0 0 16 16"><circle cx="8" cy="8" r="8" fill="#0a1f4d"/><rect x="4" y="7" width="8" height="2" fill="#fff"/><rect x="7" y="4" width="2" height="8" fill="#fff"/></svg>
</div>

<footer class="footer">
  <div class="footer-badge">CLAIM<br>GUARD<br>PLAN</div>
  <h3 style="left:356px">Quick Links</h3>
  <ul class="footer-links" style="left:356px">
    <li><svg width="14" height="12" viewBox="0 0 14 12"><path d="M0 5h9V1l5 5-5 5V7H0z" fill="#fff"/></svg>HOME</li>
    <li><svg width="14" height="12" viewBox="0 0 14 12"><path d="M0 5h9V1l5 5-5 5V7H0z" fill="#fff"/></svg>ABOUT</li>
    <li><svg width="14" height="12" viewBox="0 0 14 12"><path d="M0 5h9V1l5 5-5 5V7H0z" fill="#fff"/></svg>SERVICES</li>
    <li><svg width="14" height="12" viewBox="0 0 14 12"><path d="M0 5h9V1l5 5-5 5V7H0z" fill="#fff"/></svg>FAQ</li>
  </ul>
  <h3 style="left:548px">Other Links</h3>
  <ul class="footer-links" style="left:548px">
    <li><svg width="14" height="12" viewBox="0 0 14 12"><path d="M0 5h9V1l5 5-5 5V7H0z" fill="#fff"/></svg>CONTACT US</li>
    <li><svg width="14" height="12" viewBox="0 0 14 12"><path d="M0 5h9V1l5 5-5 5V7H0z" fill="#fff"/></svg>TERMS OF SERVICE</li>
    <li><svg width="14" height="12" viewBox="0 0 14 12"><path d="M0 5h9V1l5 5-5 5V7H0z" fill="#fff"/></svg>PRIVACY POLICY</li>
  </ul>
  <h3 style="left:800px">Contact Us</h3>
  <div class="contact-row" style="top:122px">
    <span class="contact-icon"><svg width="14" height="16" viewBox="0 0 24 24"><path fill="#fff" d="M12 2a7 7 0 0 0-7 7c0 5 7 13 7 13s7-8 7-13a7 7 0 0 0-7-7zm0 9.5a2.5 2.5 0 1 1 0-5 2.5 2.5 0 0 1 0 5z"/></svg></span>
    <span>4820 COPPER RIDGE BLVD., SUITE<br>210, MESA VERDE, ARIZONA 85000</span>
  </div>
  <div class="contact-row" style="top:204px;align-items:center">
    <span class="contact-icon"><svg width="15" height="12" viewBox="0 0 24 18"><path fill="#fff" d="M0 2l12 8 12-8V0H0zm0 3v13h24V5l-12 8z"/></svg></span>
    <span>WWW.CLAIMGUARDPLAN.EXAMPLE</span>
  </div>
  <div class="contact-row" style="top:264px;align-items:center">
    <span class="contact-icon"><svg width="14" height="14" viewBox="0 0 24 24"><path fill="#fff" d="M6.6 10.8a15.1 15.1 0 0 0 6.6 6.6l2.2-2.2c.3-.3.7-.4 1-.2 1.1.4 2.3.6 3.6.6.6 0 1 .4 1 1V20c0 .6-.4 1-1 1A17 17 0 0 1 3 4c0-.6.4-1 1-1h3.5c.6 0 1 .4 1 1 0 1.3.2 2.5.6 3.6.1.3 0 .7-.2 1z"/></svg></span>
    <span>(555) 201-4400 / (800) 555-0142</span>
  </div>
  <div class="footer-rule"></div>
  <div class="copyright">Copyrights@2023.Claim Guard Plan.All Rights Reserved</div>
  <span class="social" style="left:955px"></span>
  <span class="social" style="left:994px"></span>
  <span class="social" style="left:1032px"></span>
  <span class="social" style="left:1071px"></span>
</footer>

</body>
</html>
```